I want a business card design. the company is an infrastructure development company.

Target Market(s)

Government
real estate investors
real estate clients

Industry/Entity Type

Business

```html
<!DOCTYPE html>
<html lang="en">
<head>
<meta charset="utf-8">
<title>Vantor Crest – Business Card</title>
<link rel="stylesheet" href="https://fonts.googleapis.com/css2?family=Questrial&display=swap">
<style>
  :root {
    --page-bg: #ffffff;
    --card-top: #eef1f4;
    --card-bottom: #ffffff;
    --brand-red: #e8383b;
    --brand-blue: #3fb2e4;
    --ink: #1f1f1f;
    --card-shadow: rgba(0, 0, 0, 0.14);
  }
  * { box-sizing: border-box; margin: 0; padding: 0; }
  html, body {
    width: 1200px;
    height: 900px;
    overflow: hidden;
    background: var(--page-bg);
    font-family: "Questrial", "Century Gothic", sans-serif;
    color: var(--ink);
  }
  .canvas {
    position: relative;
    width: 1200px;
    height: 900px;
  }
  .business-card {
    position: absolute;
    left: 100px;
    top: 164px;
    width: 1000px;
    height: 571px;
    border-radius: 30px;
    overflow: hidden;
    background: linear-gradient(180deg, var(--card-top) 0%, var(--card-bottom) 45%);
    box-shadow: 0 10px 30px var(--card-shadow);
  }
  .brand-name {
    position: absolute;
    left: 64px;
    top: 74px;
    display: flex;
    align-items: center;
    gap: 22px;
    color: var(--brand-red);
    font-size: 50px;
    line-height: 1.05;
    letter-spacing: 1px;
  }
  .brand-name .brand-square {
    width: 56px;
    height: 56px;
    background: var(--brand-red);
    flex: none;
  }
  .director-block {
    position: absolute;
    right: 52px;
    top: 38px;
    text-align: right;
    font-size: 20px;
    line-height: 1.4;
  }
  .director-block .director-name {
    color: var(--brand-red);
    font-size: 23px;
  }
  .director-block .director-title {
    margin-bottom: 20px;
  }
  .company-contacts {
    position: absolute;
    left: 64px;
    top: 272px;
    font-size: 22px;
    line-height: 1.3;
  }
  .company-contacts .contact-group {
    margin-bottom: 16px;
  }
  .company-contacts .company-address {
    font-style: normal;
    margin-bottom: 0;
  }
  .card-footer {
    position: absolute;
    left: 0;
    right: 0;
    bottom: 0;
  }
  .card-footer .blue-rule {
    height: 4px;
    background: var(--brand-blue);
    margin-bottom: 5px;
  }
  .card-footer .red-band {
    height: 42px;
    background: var(--brand-red);
  }
</style>
</head>
<body>
<main class="canvas">
  <section class="business-card" aria-label="Vantor Crest business card">
    <div class="brand-name">
      <span class="brand-square" aria-hidden="true"></span>
      <span>VANTOR<br>CREST</span>
    </div>

    <div class="director-block">
      <p class="director-name">Kunle Adebanjo</p>
      <p class="director-title">MD.</p>
      <p>+234 8010000112</p>
      <p>+234 7010000467</p>
      <p>kunle@vantorcrest.com</p>
    </div>

    <div class="company-contacts">
      <div class="contact-group">
        <p>+234 10000006</p>
        <p>+234 7010000023</p>
      </div>
      <div class="contact-group">
        <p>info@vantorcrest.com</p>
        <p>www.vantorcrest.com</p>
      </div>
      <address class="contact-group company-address">
        <p>12, Marlowe street, Off Harbour</p>
        <p>Link Road, Yaba Lagos, Nigeria</p>
      </address>
    </div>

    <div class="card-footer" aria-hidden="true">
      <div class="blue-rule"></div>
      <div class="red-band"></div>
    </div>
  </section>
</main>
</body>
</html>
```